Oil and Gas Exploration and Production company needs a business card design

We need a business card design using our logo and colors in the logo. We want a mainstream design.

```html
<!DOCTYPE html>
<html lang="en">
<head>
<meta charset="utf-8">
<title>Vantor Oil &amp; Gas — Business Card</title>
<link rel="stylesheet" href="https://fonts.googleapis.com/css2?family=Lato:wght@400;700;900&display=swap">
<style>
  :root {
    --backdrop: #cdd2d3;
    --card: #232221;
    --gold: #c8961f;
    --white: #f4f4f2;
    --muted: #c9c9c6;
    --emboss: #474543;
  }
  * { box-sizing: border-box; margin: 0; padding: 0; }
  html, body { width: 1200px; height: 900px; overflow: hidden; }
  body {
    background: var(--backdrop);
    font-family: "Lato", sans-serif;
    display: flex;
    align-items: center;
    justify-content: center;
    gap: 50px;
  }
  .card {
    position: relative;
    width: 525px;
    height: 300px;
    background: var(--card);
    overflow: hidden;
  }
  .card-front .accent-band {
    position: absolute;
    left: 0; right: 0; bottom: 0;
    height: 18px;
    background: var(--gold);
  }
  .brand {
    display: flex;
    align-items: center;
    gap: 10px;
  }
  .brand-dot {
    width: 26px; height: 26px;
    border-radius: 50%;
    background: var(--gold);
    flex-shrink: 0;
  }
  .brand-name {
    font-weight: 900;
    line-height: 1.05;
    color: var(--white);
  }
  .card-front .brand {
    position: absolute;
    left: 36px;
    top: 100px;
    width: 205px;
  }
  .card-front .brand-name { font-size: 30px; }
  .divider {
    position: absolute;
    left: 262px;
    top: 82px;
    width: 2px;
    height: 118px;
    background: var(--gold);
  }
  .contact-block {
    position: absolute;
    left: 284px;
    top: 82px;
    color: var(--white);
  }
  .person-name {
    font-size: 22px;
    font-weight: 700;
    color: var(--gold);
    line-height: 1.1;
  }
  .person-title {
    font-size: 14px;
    color: var(--muted);
    margin-bottom: 14px;
  }
  .contact-list { list-style: none; }
  .contact-list li {
    display: flex;
    align-items: center;
    gap: 8px;
    font-size: 14px;
    line-height: 1.5;
  }
  .contact-list svg { width: 12px; height: 12px; flex-shrink: 0; }
  .card-back {
    display: flex;
    align-items: center;
    justify-content: center;
  }
  .card-back .brand-name { font-size: 38px; color: var(--emboss); }
  .card-back .brand-dot { width: 34px; height: 34px; background: var(--emboss); }
</style>
</head>
<body>
  <section class="card card-front">
    <div class="brand">
      <span class="brand-dot"></span>
      <span class="brand-name">Vantor Oil &amp; Gas</span>
    </div>
    <span class="divider"></span>
    <div class="contact-block">
      <p class="person-name">Daniel Hart</p>
      <p class="person-title">CEO</p>
      <ul class="contact-list">
        <li>
          <svg viewBox="0 0 12 12" aria-hidden="true"><path d="M2.5 1 L4.5 1 L5 3.5 L3.8 4.4 Q4.8 6.6 7.6 8.2 L8.5 7 L11 7.5 L11 9.5 Q10 11 8 10.6 Q2 8.6 1 3 Q1 1.5 2.5 1 Z" fill="var(--gold)"/></svg>
          (555) 014-2290
        </li>
        <li>
          <svg viewBox="0 0 12 12" aria-hidden="true"><rect x="1" y="2.5" width="10" height="7" fill="none" stroke="var(--gold)" stroke-width="1.2"/><path d="M1 2.5 L6 6.5 L11 2.5" fill="none" stroke="var(--gold)" stroke-width="1.2"/></svg>
          info@vantor-oilgas.com
        </li>
        <li>
          <svg viewBox="0 0 12 12" aria-hidden="true"><circle cx="6" cy="6" r="4.8" fill="none" stroke="var(--gold)" stroke-width="1.1"/><ellipse cx="6" cy="6" rx="2" ry="4.8" fill="none" stroke="var(--gold)" stroke-width="1"/><path d="M1.2 6 H10.8" stroke="var(--gold)" stroke-width="1"/></svg>
          www.vantor-oilgas.com
        </li>
      </ul>
    </div>
    <span class="accent-band"></span>
  </section>

  <section class="card card-back">
    <div class="brand">
      <span class="brand-dot"></span>
      <span class="brand-name">Vantor Oil &amp; Gas</span>
    </div>
  </section>
</body>
</html>
```